Luxury Business Card Design for High-End Window Treatments

Gilded Slatworks
Custom Plantation Shutters & Architectural Shading Systems

⸻

BACK

Daniel Trevick
Owner

Custom Interior & Exterior Window Treatments

919-555-0148
gildedslatworks.com

I have included a picture that I’m hoping we can use on the back, but I’m also wondering if you can get rid of the ladder? Should we get rid of shutters , shades and blinds underneath Gilded Slatworks?

Target Market(s)

High-end residential homeowners, custom home builders, architects, interior designers, and luxury renovation clients seeking premium plantation shutters and motorized architectural shading systems.

Industry/Entity Type

Custom Window treatments

Contact Information for Business Card

Front Gilded Slatworks Custom Plantation Shutters Motorized Architectural Shading Systems BACK Daniel Trevick Owner 919-555-0148 GildedSlatworks.com Custom Interior & Exterior Window Treatments By Appointment

Requirements
Nice to have
• Not 100% sure on nice to halves or the color but you can definitely check out my website to get a better understanding of what I’m trying to do

```html
<!DOCTYPE html>
<html lang="en">
<head>
<meta charset="utf-8">
<title>Gilded Slatworks – Business Card</title>
<link href="https://fonts.googleapis.com/css2?family=Montserrat:wght@400;500&family=Playfair+Display:wght@700&display=swap" rel="stylesheet">
<style>
  :root{
    --page:#e9e5dc;
    --ink:#050505;
    --gold:#c8b26b;
    --white:#f4f2ec;
    --sky:#93b2d9;
    --screen:#33373f;
    --lawn:#4f5638;
  }
  *{margin:0;padding:0;box-sizing:border-box}
  html,body{width:916px;height:1200px;overflow:hidden;background:var(--page)}
  .sheet{position:relative;width:916px;height:1200px}
  .card{position:absolute;left:73px;width:770px;height:458px;border-radius:22px;overflow:hidden;box-shadow:0 8px 22px rgba(0,0,0,.25)}
  .card--front{top:107px;background:linear-gradient(160deg,#1a1a1a 0%,var(--ink) 45%)}
  .card--back{top:640px}
  .wave{position:absolute;left:0;top:0;width:770px;height:458px}
  .brand{position:absolute;left:62px;top:150px;width:300px;text-align:center;color:var(--gold)}
  .brand__name{font-family:"Montserrat",sans-serif;font-weight:400;font-size:38px;line-height:48px;letter-spacing:.5px}
  .brand__tagline{margin-top:14px;font-family:"Montserrat",sans-serif;font-weight:500;font-size:17px;word-spacing:10px}
  .divider{position:absolute;left:393px;top:126px;width:2px;height:200px;background:var(--gold)}
  .contact{position:absolute;left:420px;top:120px;color:var(--white);font-family:"Montserrat",sans-serif}
  .contact__name{font-family:"Playfair Display",serif;font-weight:700;font-size:28px;color:var(--gold);letter-spacing:.3px}
  .contact__role{font-size:16px;margin-top:2px}
  .contact__services{font-size:16px;line-height:22px;margin-top:12px;padding-left:3px}
  .contact__line{display:flex;align-items:center;gap:10px;font-size:17px;margin-top:10px}
  .contact__line:first-of-type{margin-top:16px}
  .contact__line svg{width:17px;height:17px;fill:var(--white)}
  .contact__note{font-size:16px;color:var(--gold);margin-top:16px}
  .photo{position:absolute;inset:0;background:linear-gradient(180deg,var(--sky) 0%,var(--screen) 45%,var(--screen) 60%,var(--lawn) 100%)}
  .back-brand{position:absolute;left:500px;top:112px;width:190px;text-align:center}
  .back-brand__name{font-family:"Montserrat",sans-serif;font-weight:400;font-size:27px;line-height:34px;color:var(--white)}
  .back-brand__tagline{margin-top:8px;font-family:"Montserrat",sans-serif;font-weight:500;font-size:13px;word-spacing:6px;color:var(--gold)}
</style>
</head>
<body>
<main class="sheet">
  <section class="card card--front">
    <svg class="wave" viewBox="0 0 770 458" aria-hidden="true">
      <defs>
        <linearGradient id="goldFill" x1="0" y1="0" x2="1" y2="0">
          <stop offset="0" stop-color="#cdb874"/>
          <stop offset=".5" stop-color="#bfa862"/>
          <stop offset="1" stop-color="#d4c07e"/>
        </linearGradient>
      </defs>
      <path d="M0 385 C60 362 150 352 240 362 C360 376 470 412 590 410 C670 408 730 385 770 368 L770 458 L0 458 Z" fill="url(#goldFill)"/>
      <path d="M205 356 C330 352 440 408 560 416 C650 420 720 400 770 378 L770 388 C720 412 650 432 560 428 C440 422 330 370 205 356 Z" fill="var(--ink)"/>
    </svg>

    <div class="brand">
      <p class="brand__name">Gilded<br>Slatworks</p>
      <p class="brand__tagline">Shutters Shades Blinds</p>
    </div>

    <div class="divider"></div>

    <div class="contact">
      <p class="contact__name">Daniel Trevick</p>
      <p class="contact__role">Owner</p>
      <p class="contact__services">Custom Interior &amp; Exterior<br>Window Treatments</p>
      <p class="contact__line">
        <svg viewBox="0 0 24 24" aria-hidden="true"><path d="M3 8c0-3 4-4 9-4s9 1 9 4v2h-5V8H8v2H3zM6 11h12l3 8H3zm6 2a2.5 2.5 0 1 0 0 5 2.5 2.5 0 0 0 0-5z"/></svg>
        919-555-0148
      </p>
      <p class="contact__line">
        <svg viewBox="0 0 24 24" aria-hidden="true"><path d="M12 2a10 10 0 1 0 0 20 10 10 0 0 0 0-20zm-1 3 2 2-2 3-3-1-2 3 2 3h3l1 4a8 8 0 0 1-7-13zm3 0a8 8 0 0 1 5 12l-2-3-3 1-1-3 3-2z"/></svg>
        GildedSlatworks.com
      </p>
      <p class="contact__note">By Appointment</p>
    </div>
  </section>

  <section class="card card--back">
    <div class="photo" role="img" aria-label="Photograph of a home's covered back porch with dark exterior solar screens lowered, sky and trees above, lawn and chairs in front"></div>
    <div class="back-brand">
      <p class="back-brand__name">Gilded<br>Slatworks</p>
      <p class="back-brand__tagline">Shutters Shades Blinds</p>
    </div>
  </section>
</main>
</body>
</html>
```